PowerPoint Listing Presentation for Real Estate Agency

We need a PowerPoint presentation for a new real estate brokerage team.

[[[[[[submit 1-3 sample slides for review - i will provide feedback and you can make changes if you want to - we will not be deciding on a design prior to the deadline]]]]]

******ATTN: DESIGNERS, if your skills are webdesign then just look at this like a portable website or a brochure. it should be easy enough******

NOTE: we have all the data to put into the slides. You just need to come up with the design and layout. we have a sample design that we like and have provided.

This focus will be for the home listing side of the business (a presentation for home sellers to convince them to use our services). The data and slides will present our team and the benefits, in the best light, to use our services over that of other real estate agent applying for the job. This presentation will proved facts and benefits and describe our special and unique offerings that will show a home seller why we can sell their home for more money in less time and with the least amount of hassle. The main color scheme is Dark Blue and White (we want some additional colors included - based on your creativity. otherwise the presentation will too monotone). We would like to see the use of Statistical Graphs (3-D) - data provided. We have photos of our team and a new logo (the logo could have some minor adjustment to clean it up if necessary) - also uploaded. We have about 80-90% of the information that will be put into the slides and will need to work closely to get the design and data integrated into the presentation (should be easier then it sounds). We should be able to add slides and data 'at will' over time via our master slides built into the presentation. We have a pretty good sample presentation that we like and can be used as a guideline (this is from our affiliated business network and we have full rights to all the information), it is uploaded but doesn't contain all the slide because of size limitations.

NOTE: An additional buyers presentation will be needed after we get the sellers presentation completed, which means additional work.

This should be enough to get you started and we are available if you have any questions to help you with the project. there will be around 60-70 total slides. once concept is completed it will be easy to create the slides.

Target Market(s)

home sellers. people who are moving to a new and better home or relocation for job reasons. typically more established in life

Industry/Entity Type

Real Estate

Requirements
Must have
• all the slides must be congruent. in other words, the exact same layout feel should used across the board. we are working on building our trade dress/image. Also, it must have a soft and inviting overall feel, yet show strength of ability.
Nice to have
• nice to have use of real people images when necessary. 3D graphs would be nice. clean modern look and feel, yet sophisticated and professional.
Should not have
• should not have a lot of time consuming transitions. do not include 3D stick figures or distracting moving gifs

```html
<!DOCTYPE html>
<html lang="en">
<head>
<meta charset="utf-8">
<title>You'll Receive Superior Results</title>
<link href="https://fonts.googleapis.com/css2?family=Libre+Baskerville&display=swap" rel="stylesheet">
<style>
  :root {
    --navy: #0f2a5c;
    --navy-deep: #0a2150;
    --sky: #4d8ee0;
    --gold: #f5b21a;
    --ink: #17305f;
    --accent: #2a5fb6;
    --paper: #ffffff;
    --wash-top: #f4f8fd;
    --wash-bottom: #dbe7f6;
    --rule: #c9ced6;
    --tick-box: #f2a93b;
    --tick-box-light: #fbd68f;
    --tick: #1d55c4;
  }
  html, body {
    margin: 0;
    padding: 0;
    width: 1200px;
    height: 900px;
    overflow: hidden;
    background: var(--paper);
  }
  .slide {
    position: relative;
    width: 1200px;
    height: 900px;
    overflow: hidden;
    font-family: "Libre Baskerville", Georgia, serif;
    background: linear-gradient(180deg, var(--wash-top) 0%, var(--wash-bottom) 100%);
  }
  .slide-shapes {
    position: absolute;
    inset: 0;
  }
  .brand {
    position: absolute;
    left: 16px;
    top: 16px;
    width: 104px;
    height: 104px;
    background: var(--paper);
    border: 3px solid var(--navy);
    box-sizing: border-box;
    display: flex;
    align-items: center;
    justify-content: center;
    text-align: center;
    color: var(--navy);
    font-size: 15px;
    line-height: 1.3;
  }
  .slide-title {
    position: absolute;
    left: 585px;
    top: 26px;
    margin: 0;
    font-weight: 400;
    font-size: 36px;
    color: var(--ink);
    white-space: nowrap;
  }
  .slide-title .highlight { color: var(--accent); }
  .title-icon {
    position: absolute;
    left: 507px;
    top: 16px;
    width: 60px;
    height: 60px;
  }
  .benefits {
    position: absolute;
    left: 68px;
    top: 318px;
    margin: 0;
    padding: 0;
    list-style: none;
  }
  .benefit {
    display: flex;
    align-items: center;
    height: 56px;
    margin-bottom: 38px;
    font-size: 32px;
    color: var(--ink);
  }
  .benefit-tick {
    width: 50px;
    height: 50px;
    margin-right: 26px;
    flex: none;
  }
  .houses-art {
    position: absolute;
    left: 985px;
    top: 770px;
    width: 200px;
    height: 110px;
    background: linear-gradient(180deg, #2e5fa8 0%, #1b3f80 100%);
    border-radius: 4px;
    opacity: 0.85;
  }
  .backdrop-art {
    position: absolute;
    left: 40px;
    top: 200px;
    width: 1100px;
    height: 590px;
    background: linear-gradient(180deg, rgba(180,200,228,0.18) 0%, rgba(170,192,222,0.32) 100%);
  }
</style>
</head>
<body>
<main class="slide">
  <div class="backdrop-art" role="img" aria-label="Faint outline of a row of houses in the background"></div>

  <svg class="slide-shapes" viewBox="0 0 1200 900" aria-hidden="true">
    <defs>
      <linearGradient id="footer-band" x1="0" y1="0" x2="0" y2="1">
        <stop offset="0" stop-color="#f1f1f1"/>
        <stop offset="1" stop-color="#d6d6d6"/>
      </linearGradient>
      <linearGradient id="header-band" x1="0" y1="0" x2="0" y2="1">
        <stop offset="0" stop-color="#ffffff"/>
        <stop offset="1" stop-color="#f3f5f8"/>
      </linearGradient>
    </defs>
    <!-- header -->
    <rect x="0" y="0" width="1200" height="102" fill="url(#header-band)"/>
    <line x1="0" y1="102" x2="1200" y2="102" stroke="var(--rule)" stroke-width="2"/>
    <!-- footer -->
    <rect x="0" y="795" width="1200" height="105" fill="url(#footer-band)"/>
    <line x1="0" y1="795" x2="1200" y2="795" stroke="#ffffff" stroke-width="2"/>
    <!-- top-left swoosh -->
    <path d="M0 0 H430 C300 70 120 170 0 300 Z" fill="var(--gold)"/>
    <path d="M0 0 H412 C290 62 110 162 0 286 Z" fill="var(--sky)"/>
    <path d="M0 0 H385 C270 55 100 150 0 262 Z" fill="var(--navy)"/>
    <!-- bottom-right swoosh -->
    <path d="M690 900 C900 810 1100 640 1200 450 V900 Z" fill="var(--gold)"/>
    <path d="M708 900 C910 815 1110 650 1200 470 V900 Z" fill="var(--sky)"/>
    <path d="M735 900 C930 820 1120 670 1200 500 V900 Z" fill="var(--navy-deep)"/>
  </svg>

  <div class="brand">Harlow<br>&amp;<br>Finch</div>

  <svg class="title-icon" viewBox="0 0 60 60" aria-hidden="true">
    <circle cx="30" cy="30" r="27" fill="var(--navy)" stroke="#d8dde6" stroke-width="3"/>
    <path d="M15 30 L30 17 L45 30" fill="none" stroke="#ffffff" stroke-width="3.5" stroke-linejoin="round"/>
    <rect x="20" y="29" width="20" height="15" fill="none" stroke="#ffffff" stroke-width="3"/>
    <rect x="27" y="34" width="6" height="6" fill="#ffffff"/>
  </svg>

  <h1 class="slide-title">You’ll Receive <span class="highlight">Superior Results</span></h1>

  <ul class="benefits">
    <li class="benefit">
      <svg class="benefit-tick" viewBox="0 0 50 50" aria-hidden="true"><circle cx="25" cy="25" r="24" fill="var(--tick-box-light)"/><rect x="12" y="12" width="26" height="26" rx="3" fill="#fff5df" stroke="var(--tick-box)" stroke-width="2.5"/><path d="M15 25 L22 33 L38 12" fill="none" stroke="var(--tick)" stroke-width="5" stroke-linecap="round" stroke-linejoin="round"/></svg>
      Our Unique Team System
    </li>
    <li class="benefit">
      <svg class="benefit-tick" viewBox="0 0 50 50" aria-hidden="true"><circle cx="25" cy="25" r="24" fill="var(--tick-box-light)"/><rect x="12" y="12" width="26" height="26" rx="3" fill="#fff5df" stroke="var(--tick-box)" stroke-width="2.5"/><path d="M15 25 L22 33 L38 12" fill="none" stroke="var(--tick)" stroke-width="5" stroke-linecap="round" stroke-linejoin="round"/></svg>
      Our Exclusive and Innovative Consumer Programs
    </li>
    <li class="benefit">
      <svg class="benefit-tick" viewBox="0 0 50 50" aria-hidden="true"><circle cx="25" cy="25" r="24" fill="var(--tick-box-light)"/><rect x="12" y="12" width="26" height="26" rx="3" fill="#fff5df" stroke="var(--tick-box)" stroke-width="2.5"/><path d="M15 25 L22 33 L38 12" fill="none" stroke="var(--tick)" stroke-width="5" stroke-linecap="round" stroke-linejoin="round"/></svg>
      Our Leading Edge Technology
    </li>
    <li class="benefit">
      <svg class="benefit-tick" viewBox="0 0 50 50" aria-hidden="true"><circle cx="25" cy="25" r="24" fill="var(--tick-box-light)"/><rect x="12" y="12" width="26" height="26" rx="3" fill="#fff5df" stroke="var(--tick-box)" stroke-width="2.5"/><path d="M15 25 L22 33 L38 12" fill="none" stroke="var(--tick)" stroke-width="5" stroke-linecap="round" stroke-linejoin="round"/></svg>
      Our Specialized Skill
    </li>
  </ul>

  <div class="houses-art" role="img" aria-label="Outline drawing of three small houses"></div>
</main>
</body>
</html>
```